Heron Loan Partners Business Card

We need a business card design for our mortgage servicing company. In addition to servicing the loans of homeowners, we help homeowners with purchasing their homes and any mortgage refinancing. We would like to see designs that use the colors in the logo attached below (gold-ish yellow and navy blue), and any other design you deem fit! The design should communicate a simpler life with smart mortgages provided by Heron.

```html
<!DOCTYPE html>
<html lang="en">
<head>
<meta charset="utf-8">
<title>Heron Loan Partners Business Card</title>
<link rel="stylesheet" href="https://fonts.googleapis.com/css2?family=Open+Sans:wght@400;600;700&display=swap">
<style>
  :root {
    --gold: #c8902a;
    --navy: #231f4f;
    --ink: #1f1d24;
    --card: #f4eee5;
    --backdrop: #d8cec0;
  }
  * { margin: 0; padding: 0; box-sizing: border-box; }
  html, body { width: 1200px; height: 1046px; overflow: hidden; }
  body {
    background: var(--backdrop);
    font-family: "Open Sans", Arial, sans-serif;
    color: var(--ink);
    position: relative;
  }
  .card {
    position: absolute;
    left: 80px; top: 240px;
    width: 1040px; height: 565px;
    background: var(--card);
    border-radius: 38px;
    overflow: hidden;
    box-shadow: 0 10px 30px rgba(60, 45, 25, 0.18);
  }
  .brand {
    position: absolute;
    left: 34px; top: 62px;
    display: flex; align-items: center; gap: 14px;
  }
  .brand-dot {
    width: 22px; height: 22px; border-radius: 50%;
    background: var(--navy);
  }
  .brand-name {
    font-size: 40px; font-weight: 700;
    color: var(--gold);
    letter-spacing: 0.3px;
  }
  .identity {
    position: absolute;
    right: 42px; top: 268px;
    text-align: right;
  }
  .person-name {
    font-size: 40px; font-weight: 700; line-height: 52px;
  }
  .person-name .first { color: var(--gold); }
  .person-name .last { color: var(--navy); }
  .person-role {
    font-size: 27px; font-weight: 600; line-height: 38px;
    color: var(--ink);
  }
  .accent-bar {
    position: absolute;
    left: 1010px; top: 276px;
    width: 30px; height: 87px;
    background: var(--gold);
  }
  .divider {
    position: absolute;
    left: 38px; top: 366px;
    width: 960px; height: 2px;
    background: var(--navy);
  }
  .contacts {
    position: absolute;
    left: 34px; top: 412px;
    list-style: none;
  }
  .contacts li {
    display: flex; align-items: center; gap: 17px;
    height: 36px;
    font-size: 26px; color: #3a3740;
  }
  .contacts svg { width: 22px; height: 22px; flex: none; }
  .address {
    position: absolute;
    right: 42px; top: 446px;
    text-align: right;
    font-size: 26px; line-height: 34px;
    color: var(--ink);
    font-style: normal;
  }
  .base-bands {
    position: absolute;
    left: 0; top: 525px;
    width: 1040px; height: 40px;
  }
</style>
</head>
<body>
  <div class="card">
    <div class="brand">
      <span class="brand-dot"></span>
      <span class="brand-name">Heron Loan Partners</span>
    </div>

    <div class="identity">
      <div class="person-name"><span class="first">Lena</span> <span class="last">Varga</span></div>
      <div class="person-role">Managing Director</div>
    </div>
    <div class="accent-bar"></div>
    <div class="divider"></div>

    <ul class="contacts">
      <li>
        <svg viewBox="0 0 24 24" aria-hidden="true"><path fill="#c8902a" d="M6.6 10.8a15.1 15.1 0 0 0 6.6 6.6l2.2-2.2a1 1 0 0 1 1-.25 11.4 11.4 0 0 0 3.6.57 1 1 0 0 1 1 1V20a1 1 0 0 1-1 1A17 17 0 0 1 3 4a1 1 0 0 1 1-1h3.5a1 1 0 0 1 1 1c0 1.25.2 2.45.57 3.6a1 1 0 0 1-.25 1z"/></svg>
        (555) 014-2290
      </li>
      <li>
        <svg viewBox="0 0 24 24" aria-hidden="true"><rect x="2" y="5" width="20" height="14" rx="2" fill="#c8902a"/><path d="M3 6l9 7 9-7" fill="none" stroke="#f4eee5" stroke-width="1.6"/></svg>
        info@heronloan.com
      </li>
      <li>
        <svg viewBox="0 0 24 24" aria-hidden="true"><circle cx="12" cy="12" r="10" fill="#c8902a"/><path d="M2 12h20M12 2c3 3 3 17 0 20M12 2c-3 3-3 17 0 20" fill="none" stroke="#f4eee5" stroke-width="1.3"/></svg>
        www.heronloan.com
      </li>
    </ul>

    <address class="address">
      1840 Lakeside Blvd. Suite 300<br>
      Riverton, TX 75010
    </address>

    <svg class="base-bands" viewBox="0 0 1040 40" aria-hidden="true">
      <polygon points="0,6 722,6 710,16 0,16" fill="var(--gold)"/>
      <path d="M0 21 H716 C732 21 736 6 754 6 H1040 V40 H0 Z" fill="var(--navy)"/>
    </svg>
  </div>
</body>
</html>
```